Veranix - Solution provider in business consulting

Veranix is a swiss based company providing solutions for developing markets. The business covers various fields of business consulting, such as supply chain, product costs, quality management and manufacturing management. The Business operates in a efficient, straight and solution oriented manner.
The final design should communicate these characteristics. Asian people as well as as western people shall identify the qualities of the company at first sight.
The customer needs business cards with a simple view but an recognizable design, printed in high quality. Engraved elements such as the globe or simple words are possible.
Available colors are: (RAL)
102/102/102
51/102/102
153/204/153
255/102/51
Font: Calibri

```html
<!DOCTYPE html>
<html lang="en">
<head>
<meta charset="utf-8">
<title>Veranix – Business Cards</title>
<link rel="stylesheet" href="https://fonts.googleapis.com/css2?family=Open+Sans:wght@300;400;600;700&display=swap">
<style>
  :root {
    --ink: #666666;
    --ink-dark: #555555;
    --paper: #ffffff;
    --backdrop: #e9e7e4;
  }
  * { margin: 0; padding: 0; box-sizing: border-box; }
  html, body {
    width: 1200px; height: 900px; overflow: hidden;
    background: var(--backdrop);
    font-family: "Open Sans", Calibri, sans-serif;
    color: var(--ink);
  }
  .canvas { position: relative; width: 1200px; height: 900px; }

  .card {
    position: absolute;
    background: var(--paper);
    box-shadow: 0 6px 18px rgba(0,0,0,0.12);
    overflow: hidden;
  }
  .card--front { left: 65px; top: 42px; width: 607px; height: 373px; }
  .card--back  { left: 388px; top: 505px; width: 567px; height: 352px; }

  .holder {
    position: absolute; top: 26px; width: 100%;
    text-align: center; font-size: 22px; font-weight: 700; letter-spacing: 0.3px;
  }
  .holder .role { font-size: 15px; font-weight: 400; }

  .brand {
    position: absolute; width: 100%;
    display: flex; align-items: center; justify-content: center; gap: 14px;
    font-weight: 300; color: var(--ink); letter-spacing: 1px;
  }
  .brand .dot { border-radius: 50%; background: var(--ink); }
  .card--front .brand { top: 88px; font-size: 62px; }
  .card--front .brand .dot { width: 40px; height: 40px; }
  .card--back .brand { top: 128px; font-size: 64px; }
  .card--back .brand .dot { width: 42px; height: 42px; }

  .contacts {
    position: absolute; top: 220px; font-size: 15.5px; color: #333;
    display: flex; flex-direction: column; gap: 6px;
  }
  .contacts--web { right: 302px; align-items: flex-end; }
  .contacts--phone { left: 341px; align-items: flex-start; }
  .contact { display: flex; align-items: center; gap: 8px; height: 20px; }
  .contacts--web .contact { flex-direction: row; }
  .icon { width: 13px; height: 13px; fill: var(--ink); flex: none; }

  .swoosh { position: absolute; left: 0; bottom: 0; width: 607px; height: 373px; }
  .address {
    position: absolute; bottom: 20px; left: 93px;
    color: var(--paper); font-size: 16px;
  }

  .back-url {
    position: absolute; top: 294px; width: 100%;
    text-align: center; font-size: 19px; font-weight: 700; color: var(--ink-dark);
  }
</style>
</head>
<body>
<main class="canvas">

  <section class="card card--front" aria-label="Business card front">
    <svg class="swoosh" viewBox="0 0 607 373" aria-hidden="true">
      <path d="M100,309 Q380,276 607,300 L607,322 Q380,290 100,309 Z" fill="#666666"/>
      <path d="M0,334 Q320,286 607,318 L607,373 L0,373 Z" fill="#666666"/>
    </svg>

    <h1 class="holder">MARCO HENDL - <span class="role">CEO</span></h1>

    <div class="brand"><span>veranix</span><span class="dot"></span></div>

    <div class="contacts contacts--web">
      <div class="contact">marco.hendl@veranix.ch
        <svg class="icon" viewBox="0 0 16 16"><path d="M1,3 H15 V13 H1 Z M2,4 L8,9 L14,4" fill="#666" stroke="#fff" stroke-width="1.2"/></svg>
      </div>
      <div class="contact">www.veranix.ch
        <svg class="icon" viewBox="0 0 16 16"><circle cx="8" cy="8" r="7"/><path d="M1,8 H15 M8,1 C4,5 4,11 8,15 M8,1 C12,5 12,11 8,15" fill="none" stroke="#fff" stroke-width="1"/></svg>
      </div>
    </div>

    <div class="contacts contacts--phone">
      <div class="contact">
        <svg class="icon" viewBox="0 0 16 16"><rect x="4" y="1" width="8" height="14" rx="1.5"/><rect x="5.5" y="3" width="5" height="8" fill="#fff"/></svg>
        +41 79 382 5107
      </div>
      <div class="contact">
        <svg class="icon" viewBox="0 0 16 16"><path d="M3,1 L6,1 L7,5 L5,6.5 C6,9 7,10 9.5,11 L11,9 L15,10 L15,13 C15,14 14,15 13,15 C7,15 1,9 1,3 C1,2 2,1 3,1 Z"/></svg>
        +41 71 846 2930
      </div>
    </div>

    <p class="address">Veranix GmbH Brunnenweg 8 9246 Niederau Switzerland</p>
  </section>

  <section class="card card--back" aria-label="Business card back">
    <div class="brand"><span>veranix</span><span class="dot"></span></div>
    <p class="back-url">www.veranix.ch</p>
  </section>

</main>
</body>
</html>
```